New Business Card Design

We need a business card design for a new company based in Sydney called "Haven and Hue". This is an online buisness which will have an online store providing imported homewares.
We are looking for something that is different, perhaps even in shape and using the logo that was designed by Pixel Harbor.

Attached document is a basic example I want to see more creative versions.

Target Market(s)

Homewares, Interior Design

Industry/Entity Type

Business

Contact Information for Business Card

Company Logo
Company Name
Industry area
Name
Position
Phone
Email
Website
Motto

Requirements
Must have
• Logo
Nice to have
• Social website logos - Chatterloop, Glimmoraly, Quibbly, Boardlyne, Veltrix+

```html
<!DOCTYPE html>
<html lang="en">
<head>
<meta charset="utf-8">
<title>Haven and Hue – Business Card</title>
<link href="https://fonts.googleapis.com/css2?family=Lato:wght@400;700;900&display=swap" rel="stylesheet">
<style>
  :root {
    --backdrop: #e6e6e4;
    --ink: #0b0b0b;
    --paper: #ffffff;
    --gold: #b98a3e;
    --gold-light: #d9ad62;
    --text-light: #f2f2f2;
  }
  * { margin: 0; padding: 0; box-sizing: border-box; }
  html, body { width: 1200px; height: 1000px; overflow: hidden; }
  body {
    background: var(--backdrop);
    font-family: "Lato", sans-serif;
    position: relative;
  }
  .card {
    position: absolute;
    left: 270px;
    width: 660px;
    height: 377px;
    border-radius: 22px;
    overflow: hidden;
    box-shadow: 0 10px 24px rgba(0,0,0,0.22);
  }
  .card--front { top: 80px; background: var(--ink); }
  .card--back { top: 543px; background: var(--paper); }

  .brand-name {
    position: absolute;
    font-family: "Lato", sans-serif;
    font-weight: 700;
    color: var(--paper);
    white-space: nowrap;
  }
  .card--front .brand-name {
    left: 0; right: 0; top: 160px;
    text-align: center;
    font-size: 50px;
    letter-spacing: 1px;
  }
  .card--back .brand-name {
    left: 20px; top: 168px;
    width: 240px;
    text-align: center;
    font-size: 30px;
    color: var(--ink);
  }

  .back-shapes { position: absolute; inset: 0; }

  .socials {
    position: absolute;
    top: 22px; right: 24px;
    display: flex; gap: 8px;
  }
  .social {
    display: flex; align-items: center; gap: 4px;
    font-size: 10px; font-weight: 700; color: var(--gold);
  }
  .social::before {
    content: "";
    width: 9px; height: 9px;
    border-radius: 50%;
    background: var(--gold);
  }

  .contact {
    position: absolute;
    left: 420px; top: 100px;
    color: var(--text-light);
  }
  .contact__name {
    font-size: 25px; font-weight: 900; color: var(--gold);
  }
  .contact__role { font-size: 18px; margin-bottom: 18px; }
  .contact__address { font-size: 14px; line-height: 1.35; margin-bottom: 12px; }
  .contact__line {
    display: flex; align-items: center; gap: 8px;
    font-size: 14px; line-height: 1.6;
  }
  .contact__line svg { width: 14px; height: 14px; flex: none; }
</style>
</head>
<body>

  <section class="card card--front" aria-label="Card front">
    <span class="brand-name">Haven and Hue</span>
  </section>

  <section class="card card--back" aria-label="Card back">
    <svg class="back-shapes" viewBox="0 0 660 377" preserveAspectRatio="none">
      <defs>
        <linearGradient id="goldSweep" x1="0" y1="0" x2="0" y2="1">
          <stop offset="0" stop-color="#e0b870"/>
          <stop offset="1" stop-color="#a8762c"/>
        </linearGradient>
      </defs>
      <path d="M250 0 C330 60 370 200 375 377 L660 377 L660 0 Z" fill="var(--ink)"/>
      <path d="M250 0 C320 55 352 200 358 377 L375 377 C370 200 330 60 250 0 Z" fill="url(#goldSweep)"/>
      <path d="M250 0 C292 28 320 60 340 100 C312 55 285 25 262 0 Z" fill="var(--ink)"/>
    </svg>

    <span class="brand-name">Haven and Hue</span>

    <div class="socials">
      <span class="social">Chatterloop</span>
      <span class="social">Quibbly</span>
      <span class="social">Glimmoraly</span>
      <span class="social">Boardlyne</span>
      <span class="social">Veltrix+</span>
    </div>

    <div class="contact">
      <p class="contact__name">Marcus Ellery</p>
      <p class="contact__role">Director</p>
      <p class="contact__address">Unit 4, Lantern Lane<br>Brookvale 2100 NSW AU</p>
      <p class="contact__line">
        <svg viewBox="0 0 16 16"><path d="M3 2h3l1.5 3.5-2 1.3a8 8 0 0 0 3.7 3.7l1.3-2L14 10v3a1 1 0 0 1-1 1A12 12 0 0 1 2 3a1 1 0 0 1 1-1z" fill="var(--gold)"/></svg>
        0298765432
      </p>
      <p class="contact__line">
        <svg viewBox="0 0 16 16"><rect x="1" y="3" width="14" height="10" fill="var(--gold)"/><path d="M1 3l7 6 7-6" fill="none" stroke="var(--ink)" stroke-width="1.3"/></svg>
        me@havenandhue.com.au
      </p>
      <p class="contact__line">
        <svg viewBox="0 0 16 16"><g fill="none" stroke="var(--gold)" stroke-width="1.4"><circle cx="8" cy="8" r="6.5"/><ellipse cx="8" cy="8" rx="3" ry="6.5"/><path d="M1.5 8h13"/></g></svg>
        www.havenandhue.com.au
      </p>
    </div>
  </section>

</body>
</html>
```